RESIDENTIAL CONSTRUCTION

We are a company that specializes in building custom residential homes, the design should also emphasize that quality and service is our priority.

Industry/Entity Type

Construction Company

Contact Information for Business Card

Contact Person: Marcus Lindqvist
Company Address: 273 West Alder Ave San Jose , Ca 95380
Phone Number : 408-731-2946
Email Address: Stoneridgehomes517@mailvista.net

Font styles to use
Sans Serif

Colors
ec1f27

Requirements
Must have
• CSLB # 7362015
Nice to have
• needs to have same color as logo i uploaded, we will be printing these on a clear plastic card.

```html
<!DOCTYPE html>
<html lang="en">
<head>
<meta charset="utf-8">
<title>Stoneridge Builders — Business Card</title>
<link rel="stylesheet" href="https://fonts.googleapis.com/css2?family=Bebas+Neue&family=Lato:wght@400&display=swap">
<style>
  :root {
    --card-red: #c01f2f;
    --card-black: #050505;
    --card-white: #ffffff;
    --seal-fill: rgba(255, 255, 255, 0.93);
    --page-bg: #eeeceb;
  }
  * { box-sizing: border-box; margin: 0; padding: 0; }
  html, body {
    width: 1200px;
    height: 900px;
    overflow: hidden;
    background: var(--page-bg);
  }
  .card {
    position: absolute;
    left: 145px;
    top: 168px;
    width: 910px;
    height: 564px;
    background: var(--card-black);
    overflow: hidden;
  }
  .card__red-panel {
    position: absolute;
    left: 0; top: 0;
    width: 645px;
    height: 100%;
    background: var(--card-red);
  }
  .card__seal {
    position: absolute;
    left: 406px;
    top: 39px;
    width: 482px;
    height: 482px;
    border-radius: 50%;
    background: var(--seal-fill);
    display: flex;
    align-items: center;
    justify-content: center;
  }
  .brand-name {
    font-family: "Bebas Neue", sans-serif;
    font-size: 54px;
    letter-spacing: 1px;
    color: var(--card-red);
    white-space: nowrap;
  }
  .contact-name {
    position: absolute;
    left: 36px;
    top: 66px;
    font-family: "Bebas Neue", sans-serif;
    font-size: 42px;
    letter-spacing: 0.5px;
    color: var(--card-white);
  }
  .details {
    position: absolute;
    left: 36px;
    font-family: "Lato", sans-serif;
    font-size: 25px;
    line-height: 34px;
    color: var(--card-white);
  }
  .details--license { top: 275px; }
  .details--address { top: 333px; }
  .details--reach { top: 433px; }
  .details__row {
    display: flex;
    align-items: center;
    gap: 9px;
  }
  .details__icon {
    width: 20px;
    height: 20px;
    flex: none;
  }
</style>
</head>
<body>
  <section class="card" aria-label="Stoneridge Builders business card">
    <div class="card__red-panel"></div>

    <h1 class="contact-name">Marcus Lindqvist</h1>

    <p class="details details--license">CSLB # 7362015</p>

    <address class="details details--address" style="font-style: normal;">
      273 West Alder Ave San Jose<br>Ca 95380
    </address>

    <div class="details details--reach">
      <div class="details__row">
        <svg class="details__icon" viewBox="0 0 20 20" aria-hidden="true">
          <path fill="#fff" d="M2 6c0-2 3-3.5 8-3.5S18 4 18 6v1.5h-4V5.8c-1-.4-2.5-.6-4-.6s-3 .2-4 .6v1.7H2V6z"/>
          <path fill="#fff" d="M6 8h8l3 4v5H3v-5l3-4z"/>
          <circle cx="10" cy="13" r="2" fill="#c01f2f"/>
        </svg>
        <span>408-731-2946</span>
      </div>
      <div class="details__row">
        <svg class="details__icon" viewBox="0 0 20 20" aria-hidden="true">
          <rect x="1.5" y="4" width="17" height="12" fill="#fff"/>
          <path d="M2 4.5l8 6.5 8-6.5" fill="none" stroke="#c01f2f" stroke-width="1.4"/>
        </svg>
        <span>Stoneridgehomes517@mailvista.net</span>
      </div>
    </div>

    <div class="card__seal">
      <span class="brand-name">Stoneridge Builders</span>
    </div>
  </section>
</body>
</html>
```